Ecological Cosmetics (w/ Social Impact) Website

Dr. Wendelin Marovitz Naturprodukte KELVORA®, a small family-run ecological cosmetics “start-up” business (has been around since the mid 90s but only now beginning professionalize management), wishes to redesign its web presence, as part of a comprehensive “facelift” that will also encompass at a later stage its corporate identity (e.g. logo…).
We would like to prepare a new trilingual (later 3 additional languages will be added) website (www.kelvora7.at) that is symbiotic with web 2.0 enabled interwoven with a blog, news section, social networks integrated (e.g. preference/like buttons, Facebook), changing images and announcements appearing on first page, online payment services, mobile internet compatibility (e.g. iOS, Android, BlackBerry… thus no use of Flash, no need for a specific app), etc. and all the other significant trends in the e-commerce realm. The website should be easily and quickly accessible, fun to navigate, allow us to update it simply (through a content manager) and so “sexy” that people will want to return to the web, inform themselves of events and news, and hopefully also try our products.
Our company is based in Austria and specializes in the production of organic cosmetics in the mid-upper pricing range. We pride ourselves in offering natural cosmetics (the meaning of “natural” is relative and each person may have a different definition), with no petrochemical preservatives. Some of our products, such as the mineral salts and black mud powder from the Dead Sea cannot be obtained more naturally, unless you actually visit the area, thus retain all their properties. Our products are not medicine but the basic Dead Sea ingredients are used by spas and clinics in the area to treat many different skin, joint and bone affections. Our male and female customers (no distinction made will be made on our new website), primarily as of the ages of 25 to 65, buy KELVORA® because they:
• Care about the exterior and interior well-being
• Wish to look well cared, preserve their skin’s flexibility, natural splendor & properties
• Prefer natural skin care
• Nourish their skin with vital minerals/trace elements, protecting/treating their skin with natural ingredients
• Willing to pay more than average for natural cosmetics, looking for quality,
• Don’t mind spending about 15 minutes per week preparing a mud mask with some hot water.
• Bathe in water enriched with mineral salts
• Know or are surprised to find out that Dead Sea mud is one of the few, if not the only, naturally astringent (tenses the skin) muds in the world
• Help alleviate skin conditions (e.g. psoriasis, dermatitis, acne, eczema, pustules, oily skin ...), joint (e.g. rheumatism, arthritis ...) and cardiovascular disease.
Amongst the minerals in many of our products (particularly salt, mud), are sulfur and zinc, two naturally disinfecting and healing minerals, thus their common use in many dermatological drugs. Both salt and mud powder are completely natural, and without chemicals additives, quite important when dealing with sensitive or problematic skin, which reacts allergically to certain types of substances. The KELVORA line blends in both ingredients, enriching them with the highest-quality vitamins, essential oils and exceptional plant oils. Many of the competitors creams today use common ingredients such as petrolatum, paraffin (paraffinum liquidum), mineral oil, among others, which are derived from oil, are cheap ingredients (higher margins!) and clog pores!
To underline that this is not a chimera, there are quite a few researchers/scientists/doctors who have written articles about the benefits of the Dead Sea and its naturally occurring substances. Below are some links to abstracts of research papers, which are helpful in understanding the therapeutic potential of the black mud powder and mineral salt:
http://onlinelibrary.wiley.com/doi/10.1111/j.1365-4362.1995.tb03599.x/abstract
http://onlinelibrary.wiley.com/doi/10.1111/j.1365-4632.2005.02079.x/full
http://onlinelibrary.wiley.com/doi/10.1046/j.1365-4362.1997.00204.x/abstract
http://ard.bmj.com/content/49/2/99.short
http://www.springerlink.com/content/pv46n2p1m9p3k131/
http://onlinelibrary.wiley.com/doi/10.1111/j.1365-4632.2005.02621.x/full
http://journals.lww.com/jclinrheum/Abstract/2002/08000/Therapy_With_Mud_Compresses_for_Knee.3.aspx
http://onlinelibrary.wiley.com/doi/10.1111/j.1468-3083.1997.tb00509.x/abstract
http://onlinelibrary.wiley.com/doi/10.1046/j.1529-8019.2003.01622.x/full
http://onlinelibrary.wiley.com/doi/10.1046/j.1365-4362.1999.00583.x/full
The following links lead you to KELVORA® product data, mineral characteristics and a video of how to prepare a facial mud mask:
http://www.kelvora7.at/descargaanalisis.htm
http://www.kelvora7.at/estudio.htm
http://www.clipverse.example/watch?v=Qm4TzLp8WxR
We would like to convey, through our striking and attractive new graphic design, our values to potential clients: quality, 100% natural product, effectiveness, seriousness, confidence, respect for the environment, people, animals (the products are not tested on animals), all of which has a price (they are not cheap!). To put our money where our mouth is and contribute to transforming our planet into a better place, we are discussing with NGOs donating a percentage of certain product sales to support their causes.
Our web currently is available in 3 languages: German, Spanish and English, however, we plan to expand it by another 2 to 3 languages (Portuguese, Russian, Chinese). We are looking for a graphic design that will communicate our values and captivate people's attention, thereby helping us increase sales, projecting a solid and elegant image of reliability, effectiveness, simplicity and trust. Although we are not, and do not wish to, market our products as medicine, we do want to express, through our new graphic design, the fact that these products can be used to treat all types of skin, mitigate certain skin affections (e.g. psoriasis, dermatitis, acne, eczema, sensitive skin), and, depending on each organism’s reaction, different ailments (e.g. arthritis, rheumatism), although they won’t cure them (they can alleviate!).
To get an idea of our company, I invite you to explore our website, www.kelvora7.at, and see photos of our products. Attached please find some photos of our products, including the newly designed black mud powder box. We would like to create a unified corporate image. At this point we know that some, if not all, packages do not convey quality nor our values – this is something we wish to gradually change as each products’ graphic design and packaging gets renewed, consistent with the new brand image. This is work-in-progress and will be addressed as the company grows and has the financial capacity to invest in new design and packaging. We are advancing step by step.
Content-wise, we would provide you with product photos, and the texts to be inserted, but would like to complement these with other photos (e.g. from photobanks that include images of the Dead Sea, beaches, plants, nature…). The design should quickly associate the Internet user/visitor of our website with our values and the idea of quality products. A content manager will be used to update and modify our product portfolio.
Although some people will find us by typing into their web browser the address of our website, many will use search engines to locate us on the WWW. For this purpose, it would also be important that kelvora7.at’s different webpages can be referenced, searched for keywords and allow analysis of webtraffic (e.g. Google Analytics…).
Two colors are being used in our packages, green Pantone No. 326 and blue Pantone No. 072. We are completely flexible in terms of colors.
We hope you find the project interesting. Any questions, please do not hesitate to contact us. Thank you very much for your time, recommendations and proposals. Ideally we can close this project in about 14 days.
Information to be considered and/or included in the design:
• The web will feature an e-commerce shop, whose design should also be included in your creative proposal.
• Cosmetics tend to be divided along the lines of skin types, yet as the KELVORA line is still quite small, we have decided to divide it along treatment areas: hair, face, body. Each product is indicated for a particular skin type.
• Keyword Search box for the entire website
The current web is slow, all in Flash, difficult to navigate, has too many intermediate stages, does not offer a keyword search function, nor incorporate any web 2.0 features. Furthermore, it is more difficult to find and index in search engines as none of the pages have specific web addresses. In terms of intermediate pages, these should be eliminated shortening the time the user needs to obtain the desired information (e.g. the landing page where you choose sex & language, followed by drop of water being filled up), such that the visitor is directly lead to the main page (equal to the landing page). At first glance, the blue background and the drop of water filling up may lead the visitor to believe we are dedicated to something with water, perhaps even plumbing or purification services – such an impression must be avoided. Perhaps one of the ways to analyze all the aspects to be incorporated is an evaluation of our current web’s weaknesses and prepare a design where those are all addressed.
Target Market(s)
Male & female customers, approx. age 18-65, who care about their exterior and interior well being, “worried” about their skin, willing to pay more tha
Industry/Entity Type
Graphic Design
Requirements
Must have
- • The web will also feature a blog and an e-commerce shop, whose designs should also be included in your creative proposal.
• Address current and future languages
Content-wise, we will product photos, and the texts to be inserted, but would like to complement these with other photos (e.g. from photobanks that include images of the Dead Sea, beaches, plants, nature…). The design should quickly associate the Internet user/visitor of our website with our values and the idea of quality products. A content manager will be used to update and modify our product portfolio, as well as effects announcements on the landing page.

```html
<!DOCTYPE html>
<html lang="en">
<head>
<meta charset="utf-8">
<title>KELVORA® Naturprodukte – Dead Sea Cosmetics</title>
<link href="https://fonts.googleapis.com/css2?family=Arimo:wght@400;700&family=Open+Sans:ital,wght@0,400;0,700;1,700&family=Roboto+Condensed:wght@700&display=swap" rel="stylesheet">
<style>
:root{
  --cyan:#2fe0e8;
  --navy:#14285e;
  --bar-top:#3a3a3a;
  --bar-bottom:#0d0d0d;
  --text:#222;
  --panel:#ffffff;
  --red:#d8252b;
}
*{box-sizing:border-box;margin:0;padding:0}
html,body{width:1014px;height:1200px;overflow:hidden}
body{position:relative;font-family:"Arimo",Arial,sans-serif;color:var(--text);background:#fff}
.abs{position:absolute}

/* header scene */
.header-scene{left:0;top:0;width:1014px;height:525px;
  background:linear-gradient(180deg,#6fa8d8 0%,#a9cdea 22%,#dfeaf3 34%,#2d8fa8 48%,#4fbcc2 62%,#bfe3dc 80%,#e7dfcc 100%)}
.site-tabs{left:454px;top:0;width:157px;height:22px;background:linear-gradient(#1b8fae,#0b6784);border-radius:0 0 4px 4px;color:#fff;font-size:11px;text-align:center;line-height:21px}
.util-links{left:625px;top:0;width:253px;height:22px;background:linear-gradient(#4a4a4a,#1f1f1f);border-radius:0 0 4px 4px;font-size:11.5px;line-height:22px;padding-left:24px;word-spacing:8px}
.util-links span{color:var(--cyan)}
.logo-disc{left:109px;top:17px;width:138px;height:138px;border-radius:50%;background:#fff;border:3px solid #dfe6ef;display:flex;align-items:center;justify-content:center}
.logo-name{font-weight:700;font-size:19px;color:var(--navy);letter-spacing:.5px}
.call{right:130px;top:48px;font-size:19px;color:#2a2a2a}
.search{left:698px;top:94px;width:187px;height:24px;background:#f4f4f4;border:1px solid #c9c9c9;font-size:8.5px;color:#999;line-height:22px;padding-left:7px}
.search-btn{right:0;top:0;width:22px;height:22px;background:#ddd;border-left:1px solid #c9c9c9}
.langs{left:721px;top:141px;font-size:11px;color:#111;display:flex;align-items:center;gap:4px}
.flag{width:26px;height:16px;display:inline-block}
.flag-en{background:#23407e}
.flag-de{background:linear-gradient(#000 0 33%,#d00 33% 66%,#fc0 66%)}
.flag-es{background:linear-gradient(#c60b1e 0 25%,#ffc400 25% 75%,#c60b1e 75%)}
.langs .lbl{margin-right:9px}
.main-nav{left:102px;top:162px;width:770px;height:36px;background:linear-gradient(var(--bar-top),var(--bar-bottom));display:flex;align-items:center;padding-left:16px;gap:18px;font-size:13.5px}
.main-nav a{color:var(--cyan);text-decoration:none}

/* hero */
.hero{left:102px;top:202px;width:768px;height:322px;background:#fff;padding:4px}
.hero-stage{position:relative;width:760px;height:314px;overflow:hidden}
.hero-visual{position:absolute;left:0;top:0;width:760px;height:232px;background:linear-gradient(90deg,#5f9e98 0%,#8fbfb7 35%,#c9e0dc 60%,#dbe9e6 80%,#b9d3cf 100%)}
.hero-sea{position:absolute;left:300px;top:130px;width:400px;height:102px;background:linear-gradient(170deg,rgba(255,255,255,0) 0%,rgba(240,244,240,.75) 45%,rgba(150,200,195,.6) 100%)}
.hero-jar{position:absolute;left:90px;top:36px;width:140px;height:160px;border-radius:10px;background:linear-gradient(#57b7b3,#2f9591 55%,#c4dcdc)}
.hero-band{position:absolute;left:0;top:233px;width:760px;height:81px;background:#231f23}
.hero-model{position:absolute;left:590px;top:0;width:170px;height:314px;border-radius:60px 0 0 0;background:linear-gradient(180deg,#3b332d 0%,#b08c74 30%,#8a6a58 55%,#2b2420 80%,#1d1a1a 100%)}
.hero-line{left:482px;font-family:"Open Sans",sans-serif;font-style:italic;font-weight:700;font-size:19px;color:#fff;letter-spacing:-.2px;white-space:nowrap}
.dots{left:138px;top:479px;display:flex;gap:9px}
.dot{width:15px;height:15px;border-radius:50%;background:#444;border:2px solid #8fb7c6}
.dot.on{background:#59c9f2;border-color:#bfe9fa}

/* content */
.content-bg{left:0;top:524px;width:1014px;height:414px;background:linear-gradient(#e8e8e8,#d6d6d6)}
.hero-shadow{left:125px;top:524px;width:760px;height:10px;background:radial-gradient(ellipse at top,rgba(0,0,0,.35),transparent 70%)}
.section-title{left:114px;top:540px;font-size:22px;color:#333;font-weight:400}
.products{left:113px;top:573px;width:503px;height:313px;background:var(--panel);border:1px solid #c8c8c8;border-radius:4px}
.product{width:150px;text-align:center}
.product-img{width:124px;height:76px;margin:0 auto;background:linear-gradient(135deg,#f1f1f1,#d8dde0)}
.product-img.green{width:40px;background:linear-gradient(#eef6e8,#8fc24f)}
.product-img.violet{width:40px;background:linear-gradient(#f3f3f3,#7b3a5e)}
.product-img.gold{width:100px;background:linear-gradient(135deg,#eef5e6,#e4caa0)}
.product-img.pale{width:60px;background:linear-gradient(#f5f7ee,#dfe4c8)}
.product-img.orange{width:100px;background:linear-gradient(#f7f3ec,#f0a867)}
.caption{font-size:8.5px;color:#333;margin-top:10px}
.btns{display:flex;justify-content:center;gap:5px;margin-top:7px}
.btn{width:60px;height:21px;background:linear-gradient(#444,#1c1c1c);color:#fff;font-size:8px;line-height:21px;border-radius:2px}
.rule{left:131px;top:733px;width:465px;height:1px;background:#c9c9c9}
.pager{left:390px;top:902px;font-size:9.5px;color:#333;word-spacing:5px}

.recent{left:644px;top:537px;width:223px;height:178px;background:#f2f2f2;border:1px solid #cfcfcf}
.recent-head{height:27px;background:linear-gradient(#3c3c3c,#0e0e0e);color:var(--cyan);font-size:13px;line-height:27px;padding-left:13px}
.recent-img{left:12px;top:33px;width:99px;height:65px;background:linear-gradient(135deg,#f5f0dc,#e7d27a)}
.recent-title{left:120px;top:52px;font-size:10.5px;color:#222;white-space:nowrap}
.recent-text{left:26px;top:117px;font-size:8px;color:#333;line-height:16px;white-space:nowrap}
.recent-more{left:147px;top:153px;font-size:9px;color:var(--red);white-space:nowrap}

.ad{left:646px;top:723px;width:217px;height:180px;background:#fff;border:1px solid #bbb}
.ad-photo{left:13px;top:8px;width:85px;height:170px;background:linear-gradient(#8c6a55,#2e3a66 55%,#4a6fa0)}
.ad-brand{left:95px;top:19px;width:122px;text-align:center;font-size:12.5px;letter-spacing:1px;color:#222}
.ad-sign{left:115px;top:46px;width:74px;height:32px;border-radius:6px;background:linear-gradient(#e6474b,#a8161a);color:#fff;font-size:14px;text-align:center;line-height:32px}
.ad-lines{left:95px;top:84px;width:122px;text-align:center;font-size:7.5px;color:#111;line-height:17.5px}
.ad-lines .big{font-size:11px;letter-spacing:1px}
.ad-mark{right:3px;top:3px;width:9px;height:9px;border-radius:50%;background:#48b9e6}

/* footer */
.footer{left:0;top:938px;width:1014px;height:187px;background:linear-gradient(#3a3a3a,#0c0c0c)}
.foot-logo{left:122px;top:975px;width:112px;height:112px;border-radius:50%;background:#fff;border:3px solid #9a9a9a;display:flex;align-items:center;justify-content:center}
.foot-logo .logo-name{font-size:16px}
.foot-nav{left:276px;top:964px;font-size:14.5px;line-height:19.3px}
.foot-nav div{color:var(--cyan)}
.vline{width:1px;background:#777}
.foot-products{left:409px;top:1029px;font-family:"Roboto Condensed",sans-serif;font-weight:700;font-size:11px;line-height:16px}
.foot-products span{background:#000;color:#fff;padding:0 2px}
.foot-info{left:740px;top:950px;width:192px;text-align:center;font-family:"Open Sans",sans-serif;font-weight:700;font-size:8.3px;line-height:10.6px;color:#fff}
.foot-info .head{font-size:10px;margin-bottom:4px}
.badges{left:758px;top:1043px;width:152px;height:75px;background:#1a1a1a;display:flex;align-items:center;justify-content:center;gap:12px}
.badge{width:28px;height:28px;border-radius:50%;background:#e8e8e8}

.bottom-scene{left:0;top:1125px;width:1014px;height:75px;background:linear-gradient(#cfe5ee,#8fc9d9 50%,#e4ecea)}
.share{left:98px;top:1139px;width:271px;height:41px;background:#fff;border-radius:5px;display:flex;align-items:center;gap:9px;padding-left:10px}
.share i{width:24px;height:24px;border-radius:50%;background:linear-gradient(#5b7fb4,#2c4f85);display:block}
.copy{left:384px;top:1147px;font-size:8.5px;color:#111;line-height:10.5px;white-space:nowrap}
.call-small{left:390px;top:1176px;font-size:15px;color:#2a2a2a}
</style>
</head>
<body>

<div class="abs header-scene" role="img" aria-label="Photo of a sunny Dead Sea beach with blue sky, clouds and turquoise water"></div>
<div class="abs site-tabs">mens site &nbsp;| &nbsp;women’ s site</div>
<div class="abs util-links"><span>Sitemap</span> <span>Links</span> <span>Contact</span> <span>Downloads</span></div>
<div class="abs logo-disc"><span class="logo-name">KELVORA®</span></div>
<div class="abs call">Call us Now! : &nbsp;123-4567-8910</div>
<div class="abs search">Search our site
  <div class="abs search-btn">
    <svg width="22" height="22" viewBox="0 0 22 22"><circle cx="10" cy="10" r="3.5" fill="none" stroke="#333" stroke-width="1.3"/><line x1="12.5" y1="12.5" x2="15.5" y2="15.5" stroke="#333" stroke-width="1.6"/></svg>
  </div>
</div>
<div class="abs langs">
  <span class="flag flag-en"></span><span class="lbl">En</span>
  <span class="flag flag-de"></span><span class="lbl">De</span>
  <span class="flag flag-es"></span><span class="lbl">Es</span>
</div>
<nav class="abs main-nav">
  <a>KELVORA</a><a>Dead Sea</a><a>Aromatherapy</a><a>Facial Care</a><a>Body Care</a><a>Hair Care</a><a style="margin-left:8px">SPA’s</a>
</nav>

<section class="abs hero">
  <div class="hero-stage">
    <div class="hero-visual" role="img" aria-label="Blurred turquoise Dead Sea shoreline with white salt banks"></div>
    <div class="hero-sea"></div>
    <div class="hero-jar" role="img" aria-label="Turquoise cream jar resting on sea salt crystals"></div>
    <div class="hero-band"></div>
    <div class="hero-model" role="img" aria-label="Woman covered in Dead Sea black mud treatment"></div>
  </div>
</section>
<div class="abs hero-line" style="top:222px">NATURAL SKIN CARE</div>
<div class="abs hero-line" style="top:252px">&amp; CLEANSING TREATMENT</div>
<div class="abs hero-line" style="top:282px">from DEAD SEA</div>
<div class="abs hero-line" style="top:472px">ALL SKIN TYPES</div>
<div class="abs dots"><span class="dot on"></span><span class="dot"></span><span class="dot"></span><span class="dot"></span></div>

<div class="abs content-bg"></div>
<div class="abs hero-shadow"></div>
<h2 class="abs section-title">Our Products</h2>
<div class="abs products"></div>

<div class="abs product" style="left:123px;top:590px"><div class="product-img" role="img" aria-label="Cold cream jar and box"></div><div class="caption">Duis aute irure dolor</div><div class="btns"><span class="btn">View more</span><span class="btn">Buy this</span></div></div>
<div class="abs product" style="left:285px;top:590px"><div class="product-img green" role="img" aria-label="Green body lotion bottle"></div><div class="caption">Duis aute irure dolor</div><div class="btns"><span class="btn">View more</span><span class="btn">Buy this</span></div></div>
<div class="abs product" style="left:448px;top:590px"><div class="product-img violet" role="img" aria-label="Serum bottle"></div><div class="caption">Duis aute irure dolor</div><div class="btns"><span class="btn">View more</span><span class="btn">Buy this</span></div></div>
<div class="abs rule"></div>
<div class="abs product" style="left:123px;top:749px"><div class="product-img gold" role="img" aria-label="Skin care set and foundation tube"></div><div class="caption">Duis aute irure dolor</div><div class="btns"><span class="btn">View more</span><span class="btn">Buy this</span></div></div>
<div class="abs product" style="left:285px;top:749px"><div class="product-img pale" role="img" aria-label="Face cream tubes"></div><div class="caption">Duis aute irure dolor</div><div class="btns"><span class="btn">View more</span><span class="btn">Buy this</span></div></div>
<div class="abs product" style="left:448px;top:749px"><div class="product-img orange" role="img" aria-label="Sea buckthorn care range"></div><div class="caption">Duis aute irure dolor</div><div class="btns"><span class="btn">View more</span><span class="btn">Buy this</span></div></div>
<div class="abs pager">Front&lt;&lt; 1 2 3 4 . . . . . 8 9 10 &gt;&gt;Last</div>

<aside class="abs recent">
  <div class="recent-head">Recent Products</div>
  <div class="abs recent-img" role="img" aria-label="Assorted skin care bottles and jars"></div>
  <div class="abs recent-title">Duis aute irure dolor</div>
  <div class="abs recent-text">Lorem Ipsum has been the industry's standard<br>dummy text ever since the 1500s,</div>
  <div class="abs recent-more">View more...</div>
</aside>

<aside class="abs ad">
  <div class="abs ad-photo" role="img" aria-label="Model in a star-print top and jeans"></div>
  <div class="abs ad-mark"></div>
  <div class="abs ad-brand">THREADMARKET</div>
  <div class="abs ad-sign">Sign Up</div>
  <div class="abs ad-lines"><span class="big">FOR STYLE</span><br>25,000+ PRODUCTS<br>FREE SHIPPING<br>CASH ON DELIVERY<br>GET 500 BONUS POINTS</div>
</aside>

<footer class="abs footer"></footer>
<div class="abs foot-logo"><span class="logo-name">KELVORA®</span></div>
<div class="abs foot-nav"><div>KELVORA</div><div>Dead Sea</div><div>Aromatherapy</div><div>Facial Care</div><div>Body Care</div><div>Hair Care</div><div>SPA's</div></div>
<div class="abs vline" style="left:383px;top:963px;height:130px"></div>
<div class="abs foot-products"><span>KELVORA® Mineralschlammpulver</span><br><span>KELVORA® Black Mud Powder</span><br><span>KELVORA® Black Mud Powder</span><br><span>KELVORA® Barro Negro Mineral</span></div>
<div class="abs vline" style="left:718px;top:963px;height:130px"></div>
<div class="abs foot-info">
  <div class="head">INCI: LIMUS.</div>
  Manufactured by<br>KELVORA® NATURPRODUKTE<br>DR. WENDELIN MAROVITZ<br>Lindenweg 14, 2140<br>Auenfeld, Austria<br>www.kelvora7.at | info@kelvora7.at
</div>
<div class="abs badges"><span class="badge"></span><span class="badge"></span><span class="badge"></span></div>

<div class="abs bottom-scene" role="img" aria-label="Shoreline with shallow turquoise sea"></div>
<div class="abs share" aria-label="Social sharing buttons"><i></i><i></i><i></i><i></i><i></i><i></i><i></i><i></i></div>
<div class="abs copy">Copyright ©2011 by KELVORA NATURPRODUKTE DR. WENDELIN MAROVITZ. All rights reserved.<br>www.kelvora7.at &nbsp; Email: info@kelvora7.at</div>
<div class="abs call-small">Call us Now! : &nbsp;123-4567-8910</div>

</body>
</html>
```